KTR Design Business Card

I need to develop a business card for my real estate design and investment company. Something clean, classic and professional with a modern vibe.

Industry/Entity Type

Real Estate

Font styles to use
Serif
Sans Serif

```html
<!DOCTYPE html>
<html lang="en">
<head>
<meta charset="utf-8">
<title>KTR Design Business Card</title>
<link rel="stylesheet" href="https://fonts.googleapis.com/css2?family=Arimo:wght@400;500&display=swap">
<style>
  :root {
    --backdrop: #e3e3e3;
    --paper: #f4f4f4;
    --ink: #1e1e1e;
    --ink-soft: #2a2a2a;
    --on-dark: #f2f2f2;
    --on-dark-muted: #d9d9d9;
  }
  html, body {
    margin: 0;
    padding: 0;
    width: 1200px;
    height: 720px;
    overflow: hidden;
    background: var(--backdrop);
    font-family: "Arimo", Arial, sans-serif;
  }
  .canvas {
    position: relative;
    width: 1200px;
    height: 720px;
  }
  .card {
    position: absolute;
    top: 242px;
    width: 420px;
    height: 239px;
    overflow: hidden;
  }
  .card--front { left: 147px; background: var(--paper); }
  .card--back { left: 633px; background: linear-gradient(160deg, #2b2b2b, #151515); }

  .brand {
    position: absolute;
    left: 0;
    right: 0;
    display: flex;
    align-items: center;
    justify-content: center;
    gap: 8px;
    font-weight: 400;
    letter-spacing: 0.04em;
  }
  .brand__square {
    width: 9px;
    height: 9px;
    background: currentColor;
  }
  .card--front .brand { top: 44px; color: var(--ink); font-size: 26px; }
  .card--back .brand { top: 98px; color: var(--on-dark); font-size: 32px; }

  .name-band {
    position: absolute;
    left: 0;
    top: 120px;
    width: 100%;
    height: 33px;
    background: var(--ink);
    color: var(--on-dark);
    display: flex;
    align-items: center;
    justify-content: center;
    gap: 4px;
  }
  .name-band__name { font-size: 14px; font-weight: 500; }
  .name-band__role { font-size: 10px; color: var(--on-dark-muted); }

  .contact-panel {
    position: absolute;
    left: 0;
    top: 163px;
    width: 100%;
    height: 76px;
    background: linear-gradient(180deg, var(--ink-soft), var(--ink));
    color: var(--on-dark);
  }
  .contact-list {
    list-style: none;
    margin: 0;
    padding: 0;
    position: absolute;
    left: 19px;
    top: 17px;
    font-size: 10px;
    line-height: 12px;
  }
  .contact-list li { display: flex; align-items: center; gap: 8px; }
  .contact-list svg { width: 10px; height: 10px; flex: none; }
  .address {
    position: absolute;
    right: 23px;
    top: 32px;
    margin: 0;
    text-align: right;
    font-size: 10px;
    line-height: 12px;
    font-style: normal;
  }
</style>
</head>
<body>
<main class="canvas">
  <section class="card card--front">
    <div class="brand"><span class="brand__square"></span>KTR Design</div>

    <div class="name-band">
      <span class="name-band__name">Ellis Morgan</span>
      <span class="name-band__role">| Founder &amp; CEO</span>
    </div>

    <div class="contact-panel">
      <ul class="contact-list">
        <li>
          <svg viewBox="0 0 10 10" aria-hidden="true"><path d="M1 3.5 Q5 1 9 3.5 L8 5 L6.5 4.2 V3.6 H3.5 V4.2 L2 5 Z M2.5 5.5 H7.5 L8 9 H2 Z" fill="currentColor"/></svg>
          +100 555 0142
        </li>
        <li>
          <svg viewBox="0 0 10 10" aria-hidden="true"><rect x="2.8" y="0.5" width="4.4" height="9" rx="0.8" fill="none" stroke="currentColor"/><rect x="4.4" y="7.6" width="1.2" height="0.8" fill="currentColor"/></svg>
          +100 555 0187
        </li>
        <li>
          <svg viewBox="0 0 10 10" aria-hidden="true"><rect x="0.5" y="2" width="9" height="6.5" fill="none" stroke="currentColor"/><path d="M0.5 2 L5 5.8 L9.5 2 M0.5 8.5 L4 5 M9.5 8.5 L6 5" fill="none" stroke="currentColor" stroke-width="0.8"/></svg>
          info@ktrdesign.com
        </li>
        <li>
          <svg viewBox="0 0 10 10" aria-hidden="true"><rect x="0.5" y="1" width="9" height="6" fill="none" stroke="currentColor"/><path d="M3 9.2 H7 M5 7 V9" stroke="currentColor"/></svg>
          www.ktrdesign.com
        </li>
      </ul>
      <address class="address">Here your compnay or home<br>address</address>
    </div>
  </section>

  <section class="card card--back">
    <div class="brand"><span class="brand__square"></span>KTR Design</div>
  </section>
</main>
</body>
</html>
```